Stage Design Company Business Card

We are looking to step up up our business card design for our team.

We are a Full service Design and Consultation company for Stage and TV with an emphasis in Theatrical Lighting.

We like our materials to be clean and modern with solid colors free of patterns and gradients. Our brand consists of 4 primary colors Purple, Black, Grey, and White. Provided is our Word Mark as well as our Symbol Logo.

We would like our cards to leave an impression beyond the information, show our attention to design and detail, and make our marks an easily recognized feature (together or apart) for our clients.

We need a warm approachable comfortable feel for some clients, and a professional flair for the board member type clients.

Attached are our brand elements, and our existing cards to give a sense of our style and a glipse at the information we provide on our cards.

Target Market(s)

broad client base from church leaders to high school teachers and architects.

Industry/Entity Type

Business

Contact Information for Business Card

We format our phone number with periods not parenthesis or dashes. Information will be edited for each of our team members, and team member specific cards are not part of this scope, but rather a template so to speak.

Font styles to use
Sans Serif

Colors
6b449b
ffffff
000000
333333
aaaaaa

Requirements
Must have
• Wordmark and logo mark present (does not need to exist on the same side of card)
• Brand Colors,
• Name, Phone, Email, Address.
• Unique choices that make someone stop and take a second look
Nice to have
• It would be nice to somehow convey what we DO, as our brand name does not lend itself to this, outside of an obvious tagline though.....
• social media if not crowded. all of our handles match (instagram, twitter, facebook)
Should not have
• "clipart"

```html
<!DOCTYPE html>
<html lang="en">
<head>
<meta charset="utf-8">
<title>Corvane Business Card</title>
<link rel="stylesheet" href="https://fonts.googleapis.com/css2?family=Open+Sans:ital,wght@0,400;0,600;0,700;1,700&display=swap">
<style>
  :root {
    --stage-bg: #eeeef0;
    --card-purple: #35226a;
    --card-ink: #e4e4ea;
    --card-ink-soft: #d6d6de;
  }
  * { box-sizing: border-box; margin: 0; padding: 0; }
  html, body {
    width: 1200px; height: 900px; overflow: hidden;
    background: var(--stage-bg);
    font-family: "Open Sans", Arial, sans-serif;
  }
  .canvas { position: relative; width: 1200px; height: 900px; }
  .card {
    position: absolute;
    background: var(--card-purple);
    color: var(--card-ink);
    box-shadow: 0 6px 18px rgba(0,0,0,0.18);
    overflow: hidden;
  }
  .card-front { left: 78px; top: 34px; width: 588px; height: 364px; }
  .card-back { left: 388px; top: 505px; width: 566px; height: 352px; }

  .wordmark {
    font-weight: 600;
    letter-spacing: 0.42em;
    color: var(--card-ink);
    white-space: nowrap;
  }
  .card-front .wordmark {
    position: absolute; left: 40px; top: 48px; font-size: 30px;
  }
  .brand-mark-ring {
    position: absolute; right: 22px; top: 58px;
    width: 236px; height: 236px; border-radius: 50%;
    border: 14px solid var(--card-ink);
  }
  .holder { position: absolute; left: 36px; top: 142px; }
  .holder-name { font-size: 19px; font-weight: 700; color: var(--card-ink-soft); line-height: 1.2; }
  .holder-role { font-size: 15px; line-height: 1.3; }
  .contact-list { list-style: none; position: absolute; left: 36px; top: 206px; font-size: 15px; line-height: 21px; }
  .contact-list li { display: flex; align-items: center; gap: 7px; }
  .contact-list svg { width: 12px; height: 12px; fill: var(--card-ink); flex: none; }
  .address { position: absolute; left: 36px; top: 284px; font-size: 15px; line-height: 22px; }

  .lockup {
    position: absolute; left: 84px; top: 106px;
    display: flex; align-items: center; gap: 40px;
  }
  .lockup-dot {
    width: 92px; height: 92px; border-radius: 50%;
    border: 9px solid var(--card-ink-soft);
  }
  .card-back .wordmark { font-size: 38px; color: var(--card-ink-soft); }
  .tagline {
    position: absolute; left: 0; right: 0; top: 272px;
    text-align: center; font-size: 15px; font-weight: 700; font-style: italic;
    line-height: 22px; color: #c9c9d6;
  }
</style>
</head>
<body>
<main class="canvas">
  <section class="card card-front" aria-label="Card front">
    <div class="wordmark">CORVANE</div>
    <div class="holder">
      <p class="holder-name">ELIAS MARLOW</p>
      <p class="holder-role">Managing Director</p>
    </div>
    <ul class="contact-list">
      <li><svg viewBox="0 0 24 24"><path d="M6.6 10.8a15.1 15.1 0 0 0 6.6 6.6l2.2-2.2a1 1 0 0 1 1-.25 11.4 11.4 0 0 0 3.6.57 1 1 0 0 1 1 1V20a1 1 0 0 1-1 1A17 17 0 0 1 3 4a1 1 0 0 1 1-1h3.5a1 1 0 0 1 1 1c0 1.25.2 2.45.57 3.57a1 1 0 0 1-.25 1z"/></svg>044.123.456.789</li>
      <li><svg viewBox="0 0 24 24"><path d="M2 5h20v14H2z M2 5l10 8 10-8" fill="none" stroke="#e4e4ea" stroke-width="0"/><path d="M2 6l10 7 10-7v13H2z M3 5h18l-9 6z"/></svg>info@youremail.com</li>
      <li><svg viewBox="0 0 24 24"><path d="M12 2a10 10 0 1 0 0 20 10 10 0 0 0 0-20zm6.9 6h-2.9a15.7 15.7 0 0 0-1.4-3.6A8 8 0 0 1 18.9 8zM12 4a14 14 0 0 1 1.9 4h-3.8A14 14 0 0 1 12 4zM4.3 14a8 8 0 0 1 0-4h3.4a16 16 0 0 0 0 4zm.8 2h2.9a15.7 15.7 0 0 0 1.4 3.6A8 8 0 0 1 5.1 16zM8 8H5.1a8 8 0 0 1 4.3-3.6A15.7 15.7 0 0 0 8 8zm4 12a14 14 0 0 1-1.9-4h3.8A14 14 0 0 1 12 20zm2.3-6H9.7a14.7 14.7 0 0 1 0-4h4.6a14.7 14.7 0 0 1 0 4zm.3 5.6a15.7 15.7 0 0 0 1.4-3.6h2.9a8 8 0 0 1-4.3 3.6zM16.3 14a16 16 0 0 0 0-4h3.4a8 8 0 0 1 0 4z"/></svg>www.websitename.com</li>
    </ul>
    <p class="address">1234, Address GoesHere,<br>Country name, 12345</p>
    <div class="brand-mark-ring" aria-hidden="true"></div>
  </section>

  <section class="card card-back" aria-label="Card back">
    <div class="lockup">
      <div class="lockup-dot" aria-hidden="true"></div>
      <div class="wordmark">CORVANE</div>
    </div>
    <p class="tagline">Design and Consultation company for Stage<br>and TV with an emphasis in Theatrical Lighting.</p>
  </section>
</main>
</body>
</html>
```